Realty Group Needs Classy, Contemporary Letterhead Design

We need a letterhead design for a new realty company located in NY, USA. We buy investment properties to rehabilitate and or keep in our rental portfolio.

```html
<!DOCTYPE html>
<html lang="en">
<head>
<meta charset="utf-8">
<title>Meridian Realty Group – Letterhead</title>
<link rel="stylesheet" href="https://fonts.googleapis.com/css2?family=Open+Sans:wght@400;600;700;800&display=swap">
<style>
  :root {
    --brand-purple: #4b2a8c;
    --accent-grey: #8d8d8f;
    --text-grey: #6f6f73;
    --ink: #2d2d33;
    --paper: #ffffff;
    --backdrop: #eeeeef;
    --signature-tone: #e6e6e8;
  }
  * { box-sizing: border-box; margin: 0; padding: 0; }
  html, body {
    width: 1200px; height: 795px; overflow: hidden;
    background: var(--backdrop);
    font-family: "Open Sans", sans-serif;
  }
  .canvas { position: relative; width: 1200px; height: 795px; }
  .letterhead {
    position: absolute; left: 331px; top: 17px;
    width: 537px; height: 760px;
    background: var(--paper);
    box-shadow: 0 2px 10px rgba(0,0,0,0.12);
    overflow: hidden;
  }
  .brand {
    position: absolute; left: 40px; top: 58px;
    color: var(--brand-purple); font-weight: 800;
    line-height: 1;
  }
  .brand-name { font-size: 19px; letter-spacing: 0.3px; }
  .brand-sub { font-size: 8px; margin-top: 3px; letter-spacing: 0.4px; }
  .office-address {
    position: absolute; left: 232px; top: 58px;
    font-size: 6.5px; font-weight: 700; font-style: normal;
    color: var(--ink); line-height: 1.45;
  }
  .contact-list {
    position: absolute; left: 352px; top: 52px;
    list-style: none; font-size: 6px; color: var(--text-grey); line-height: 1.6;
  }
  .contact-list li { display: flex; align-items: center; gap: 4px; }
  .contact-list .dot {
    width: 6px; height: 6px; border-radius: 50%; background: var(--brand-purple);
    display: inline-block;
  }
  .letter-body {
    position: absolute; left: 40px; top: 200px; width: 420px;
    font-size: 8.4px; color: var(--text-grey); line-height: 1.5;
  }
  .letter-date { margin-bottom: 14px; }
  .recipient { margin-bottom: 12px; }
  .salutation { font-weight: 700; color: var(--ink); margin-bottom: 12px; }
  .letter-body p.para { margin-bottom: 12px; }
  .signature {
    position: absolute; left: 330px; top: 498px; width: 92px; height: 30px;
    background: var(--signature-tone); border-radius: 3px;
    z-index: 2;
  }
  .corner-swoosh { position: absolute; left: 0; top: 0; z-index: 1; }
</style>
</head>
<body>
<div class="canvas">
  <section class="letterhead">
    <div class="brand">
      <div class="brand-name">MERIDIAN</div>
      <div class="brand-sub">Realty Group, LLC</div>
    </div>

    <address class="office-address">
      Suite 102 Street name, State,<br>
      Zip 2024 Country
    </address>

    <ul class="contact-list">
      <li><span class="dot"></span>+1 212 555 0147</li>
      <li><span class="dot"></span>+1 212 555 0198</li>
      <li><span class="dot"></span>info@meridianrealty.com</li>
      <li><span class="dot"></span>www.meridianrealty.com</li>
    </ul>

    <div class="letter-body">
      <p class="letter-date">January 12, 2014</p>
      <p class="recipient">Mr. John Doe<br>President<br>AA Corporation<br>111 Street Name, Suite#<br>City, State, 12345</p>
      <p class="salutation">Dear Mr. John,</p>
      <p class="para">Lorem Ipsum is simply dummy text of the printing and typesetting industry. Lorem Ipsum has been the industry's standard dummy text ever since the 1500s, when an unknown printer took a galley of type and scrambled it to make a type specimen book. It has survived not only five centuries, but also the leap into electronic typesetting, remaining essentially unchanged.</p>
      <p class="para">The standard chunk of Lorem Ipsum used since the 1500s is reproduced below for those interested. Sections 1.10.32 and 1.10.33 from "de Finibus Bonorum et Malorum" by Cicero are also reproduced in their exact original form, accompanied by English versions from the 1914 translation by H. Rackham.</p>
      <p class="para">Lorem Ipsum is simply dummy text of the printing and typesetting industry. Lorem Ipsum has been the industry's standard dummy text ever since the 1500s, when an unknown printer took a galley of type and scrambled it to make a type specimen book. It has survived not only five centuries, but also the leap into electronic typesetting, remaining essentially unchanged. It was popularised in the</p>
    </div>

    <div class="signature" role="img" aria-label="Handwritten signature of the sender"></div>

    <svg class="corner-swoosh" width="537" height="760" viewBox="0 0 537 760" aria-hidden="true">
      <path d="M235 760 C330 625 440 515 537 432 L537 760 Z" fill="var(--accent-grey)"/>
      <path d="M272 760 C365 635 460 540 537 470 L537 760 Z" fill="var(--paper)"/>
      <path d="M300 760 C390 640 475 555 537 500 L537 760 Z" fill="var(--brand-purple)"/>
      <path d="M392 760 C445 680 495 615 537 585 L537 760 Z" fill="var(--paper)"/>
      <path d="M455 760 C490 720 515 692 537 676 L537 760 Z" fill="var(--accent-grey)"/>
    </svg>
  </section>
</div>
</body>
</html>
```